Marbrook Cupcakes Website

We need a new website. We make Texas-size gourmet cupcakes and cupcake jars. We want a website similar to the one KEYlane is hosting and made. They're charging too much per month. I would like to have Blu Otter host it. see the current site at: marbrookcupcakes.com

```html
<!DOCTYPE html>
<html lang="en">
<head>
<meta charset="utf-8">
<title>Marbrook Cupcakes</title>
<link href="https://fonts.googleapis.com/css2?family=Bodoni+Moda:wght@400;500&family=Poppins:wght@400;500;600&display=swap" rel="stylesheet">
<style>
:root{
  --teal:#5fc0c5;
  --teal-dark:#45aeb4;
  --cocoa:#2a0c05;
  --ink:#111;
  --text:#4a4a4a;
  --white:#fff;
  --star:#e8361f;
}
*{margin:0;padding:0;box-sizing:border-box}
html,body{width:1200px;height:4566px;overflow:hidden}
body{position:relative;font-family:'Poppins',sans-serif;color:var(--ink);background:var(--white)}
.abs{position:absolute}
.serif{font-family:'Bodoni Moda',serif;font-weight:400}
.ph{position:absolute}
.btn{position:absolute;display:flex;align-items:center;justify-content:center;gap:8px;border-radius:30px;font-weight:500;font-size:15px;color:var(--white);z-index:3}
.btn .dot{width:14px;height:14px;border-radius:50%;background:var(--white);display:inline-block;position:relative}
.btn .dot::after{content:"";position:absolute;left:5px;top:4px;border-style:solid;border-width:3px 0 3px 5px;border-color:transparent transparent transparent var(--teal)}
.btn.dark .dot::after{border-left-color:var(--cocoa)}
.arrow{position:absolute;width:40px;height:40px;border-radius:50%;display:flex;align-items:center;justify-content:center;font-size:18px;font-weight:600;z-index:3}
.arrow.white{background:var(--white);color:var(--ink)}
.arrow.teal{background:var(--teal);color:var(--white)}
.arrow.light{background:var(--white);color:var(--teal-dark)}

/* top bar and header */
.topbar{left:0;top:0;width:1200px;height:32px;background:var(--teal);color:var(--white);font-size:10px;font-weight:500;text-align:center;line-height:32px;letter-spacing:.2px}
.brand-badge{left:112px;top:6px;width:124px;height:124px;border-radius:50%;background:var(--white);border:2px solid var(--teal);display:flex;align-items:center;justify-content:center;text-align:center;font-size:13px;font-weight:600;color:var(--teal-dark);line-height:1.3}
.reviews{left:503px;top:60px;font-size:14px;font-weight:600;text-decoration:underline}
.reviews::before{content:"★";color:#e58a1f;margin-right:6px;display:inline-block}
.search{left:624px;top:50px;width:337px;height:42px;border-radius:21px;background:var(--white);box-shadow:0 2px 8px rgba(0,0,0,.15);font-size:12px;color:#777;padding:12px 20px}
.search .go{position:absolute;right:6px;top:6px;width:30px;height:30px;border-radius:50%;background:var(--teal)}
.hicon{position:absolute;top:54px;width:34px;height:34px;border-radius:50%;background:var(--white);box-shadow:0 2px 6px rgba(0,0,0,.18);display:flex;align-items:center;justify-content:center}
.nav{top:125px;font-size:14px;font-weight:500}
.nav a{position:absolute;white-space:nowrap;color:var(--ink);text-decoration:none}
.nav a.active{border-bottom:2px solid var(--ink);padding-bottom:3px}

/* hero */
.hero{left:0;top:170px;width:1200px;height:600px;background:linear-gradient(90deg,#3a120a 0%,#4a1b12 28%,#2f3e3c 30%,#2c4e4c 52%,#6a2a22 55%,#8e4a3e 75%,#b56f72 80%,#c9898e 100%)}
.hero-title{left:106px;top:205px;color:var(--white);font-size:92px;line-height:1;z-index:3}
.hero-title small{font-size:60px}
.hero-title.two{left:257px;top:318px}
.hero-note{left:726px;top:262px;border-left:2px solid var(--white);padding-left:16px;color:var(--white);font-size:13px;line-height:26px;width:370px}
.hero-cake-label{left:710px;top:637px;color:var(--white);font-size:15px;font-weight:500}

/* about */
.about-ring{left:113px;top:848px;width:456px;height:456px;border-radius:50%;background:var(--teal)}
.about-photo{left:133px;top:830px;width:440px;height:495px;background:radial-gradient(circle at 50% 45%,#cfcfcf 0%,#9a9a9a 55%,#5a5a5a 100%);clip-path:circle(222px at 50% 55%)}
.about-head{left:667px;top:870px;font-size:54px}
.about-copy{left:667px;top:952px;width:430px;font-size:13.6px;line-height:25.6px;color:var(--text)}
.about-copy p+p{margin-top:19px}

/* flavours */
.flavours{left:0;top:1420px;width:1200px;height:693px;background:var(--teal)}
.section-title{left:0;width:1200px;text-align:center;font-size:54px;z-index:3}
.flavour{position:absolute;top:1624px;width:214px;text-align:center;color:var(--white)}
.flavour .img{width:214px;height:248px;background:linear-gradient(160deg,#8a4a30 0%,#5c2d1a 60%,#3a1a0e 100%)}
.flavour h3{font-size:16px;font-weight:600;margin-top:26px}
.flavour p{font-size:11.5px;line-height:19px;margin-top:6px}

/* testimonials */
.tcard{position:absolute;top:2300px;width:372px;height:199px;border-radius:50px;background:var(--white);box-shadow:0 6px 18px rgba(0,0,0,.14)}
.avatar{position:absolute;width:134px;height:134px;border-radius:50%;background:linear-gradient(160deg,#c9c9c9,#7f8a95)}
.tname{position:absolute;font-size:16px;font-weight:600;color:var(--ink)}
.stars{position:absolute;color:var(--star);font-size:16px;letter-spacing:2px}
.ttext{position:absolute;font-size:14px;line-height:25px;color:#333;width:230px}

/* occasion */
.occasion{left:0;top:2591px;width:1200px;height:425px;background:var(--cocoa)}
.occ-title{left:110px;top:2676px;color:var(--white);font-size:54px;z-index:3;white-space:nowrap}
.occ-sub{left:110px;top:2760px;color:var(--white);font-size:21px;line-height:34px;width:640px;z-index:3}

/* gallery */
.gimg{position:absolute;border-radius:4px}

/* goodness */
.goodness-box{left:131px;top:3970px;width:938px;height:302px;background:linear-gradient(135deg,var(--teal-dark),var(--teal))}
.good-title{left:131px;top:4022px;width:938px;text-align:center;color:var(--white);font-size:54px;z-index:3}
.good-sub{left:131px;top:4110px;width:938px;text-align:center;color:var(--white);font-size:20px;z-index:3}

/* footer */
.footer{left:0;top:4100px;width:1200px;height:466px;background:#000}
.f-brand{left:110px;top:4325px;width:110px;height:110px;border-radius:50%;border:2px solid var(--white);color:var(--white);font-size:13px;font-weight:600;display:flex;align-items:center;justify-content:center;text-align:center;line-height:1.3}
.fnav a{position:absolute;top:4358px;color:var(--white);font-size:13.5px;text-decoration:none;white-space:nowrap}
.f-offer{left:305px;top:4409px;color:var(--white);font-size:13px;line-height:26px;font-weight:500}
.f-email{left:585px;top:4410px;width:324px;height:39px;border-radius:20px;background:var(--white);font-size:13px;padding:10px 22px}
.f-email .go{position:absolute;right:6px;top:6px;width:27px;height:27px;border-radius:50%;background:var(--teal);color:var(--white);font-size:12px;text-align:center;line-height:27px}
.social{position:absolute;top:4350px;width:32px;height:32px;border-radius:50%;background:var(--white)}
.f-rule{left:120px;top:4490px;width:960px;height:1px;background:#555}
.copy{left:0;top:4516px;width:1200px;text-align:center;color:var(--white);font-size:11px}
</style>
</head>
<body>

<div class="abs topbar">ORDER DESSERTS FOR LOCAL PICK UP</div>
<div class="abs brand-badge">Marbrook<br>Cupcakes</div>
<div class="abs reviews">Reviews</div>
<div class="abs search">Search<span class="go"></span></div>
<div class="hicon" style="left:984px"><svg width="14" height="14" viewBox="0 0 14 14"><circle cx="7" cy="4" r="3" fill="#111"/><path d="M1 14c0-4 3-6 6-6s6 2 6 6z" fill="#111"/></svg></div>
<div class="hicon" style="left:1018px"><svg width="15" height="14" viewBox="0 0 15 14"><path d="M0 1h3l2 8h8l2-6H4" fill="none" stroke="#111" stroke-width="1.8"/><circle cx="6" cy="12" r="1.5" fill="#111"/><circle cx="12" cy="12" r="1.5" fill="#111"/></svg></div>
<div class="hicon" style="left:1052px"><svg width="14" height="13" viewBox="0 0 14 13"><path d="M7 13L1 6.5A3.5 3.5 0 0 1 7 2a3.5 3.5 0 0 1 6 4.5z" fill="#111"/></svg></div>
<nav class="abs nav">
  <a class="active" style="left:427px">Home</a>
  <a style="left:496px">About Us</a>
  <a style="left:587px">Order Online</a>
  <a style="left:702px">Flavours</a>
  <a style="left:789px">Shop</a>
  <a style="left:853px">Get Offer</a>
</nav>
<div class="btn" style="left:950px;top:113px;width:137px;height:45px;background:var(--teal);font-size:16px">Contact Us</div>

<!-- hero -->
<section class="abs hero" role="img" aria-label="Four gourmet cupcakes with swirled frosting on warm coloured panels"></section>
<div class="ph" role="img" aria-label="Raspberry cupcake" style="left:97px;top:400px;width:165px;height:220px;border-radius:60px 60px 20px 20px;background:linear-gradient(180deg,#f1e3cf 0%,#d9b89a 45%,#6d4a33 100%)"></div>
<div class="ph" role="img" aria-label="Rainbow frosted cupcake" style="left:393px;top:400px;width:174px;height:220px;border-radius:60px 60px 20px 20px;background:linear-gradient(180deg,#d86cc4 0%,#6aa8e8 40%,#27b7c2 100%)"></div>
<div class="ph" role="img" aria-label="Pink swirl cupcake with sprinkles" style="left:688px;top:400px;width:184px;height:220px;border-radius:60px 60px 20px 20px;background:linear-gradient(180deg,#f6d6e0 0%,#f1c6cf 45%,#e9c3a0 100%)"></div>
<div class="ph" role="img" aria-label="Vanilla cupcake in pink liner" style="left:987px;top:400px;width:183px;height:220px;border-radius:60px 60px 20px 20px;background:linear-gradient(180deg,#fbece6 0%,#f3d3cf 45%,#eaa8bd 100%)"></div>
<h1 class="abs hero-title serif">Big <small>on Flavor</small></h1>
<div class="abs hero-title two serif">Bigger <small>on Love</small></div>
<p class="abs hero-note">Experience Texas-size gourmet cupcakes and cupcake jars in every delightful bite</p>
<div class="abs hero-cake-label">Lorum ipsum Dolor</div>
<div class="arrow white" style="left:39px;top:477px">«</div>
<div class="arrow white" style="left:1120px;top:477px">»</div>
<svg class="abs" style="left:0;top:700px" width="1200" height="80" viewBox="0 0 1200 80"><path d="M0 34 L30 26 L52 40 L80 22 L110 36 L140 18 L170 34 L205 24 L240 38 L270 20 L300 32 L335 16 L365 34 L400 22 L430 36 L465 18 L500 30 L530 20 L565 38 L600 24 L630 34 L665 16 L700 32 L735 22 L770 38 L800 20 L835 34 L870 18 L905 36 L940 22 L975 32 L1010 16 L1045 34 L1080 22 L1110 38 L1145 20 L1175 32 L1200 24 L1200 80 L0 80Z" fill="#fff"/></svg>

<!-- about -->
<div class="abs about-ring"></div>
<div class="abs about-photo" role="img" aria-label="Portrait of the bakery owner in a dark suit"></div>
<h2 class="abs about-head serif">About Us</h2>
<div class="abs about-copy">
  <p>Lorem ipsum dolor sit amet, consectetur adipiscing elit, sed do eiusmod tempor incididunt ut labore et dolore magna aliqua. Ut enim ad minim veniam, quis nostrud exercitation ullamco laboris nisi ut aliquip ex ea commodo consequat. Duis aute irure dolor in reprehenderit in voluptate velit esse cillum dolore eu fugiat nulla pariatur. Excepteur sint occaecat cupidatat non proident, sunt in culpa qui officia deserunt mollit anim id est laborum</p>
  <p>Lorem ipsum dolor sit amet, consectetur adipiscing elit, sed do eiusmod tempor incididunt ut l</p>
</div>
<div class="btn" style="left:668px;top:1257px;width:161px;height:43px;background:var(--teal)">View More <span class="dot"></span></div>

<!-- flavours -->
<svg class="abs" style="left:0;top:1410px" width="1200" height="60" viewBox="0 0 1200 60"><path d="M0 30 L35 18 L60 30 L95 10 L125 26 L160 14 L195 30 L225 8 L260 24 L295 12 L330 28 L365 16 L400 30 L430 10 L465 26 L500 14 L535 30 L570 12 L600 24 L640 8 L675 26 L710 16 L745 30 L780 12 L815 28 L850 14 L885 30 L920 10 L955 24 L990 14 L1025 30 L1060 12 L1095 26 L1130 16 L1165 30 L1200 14 L1200 60 L0 60Z" fill="var(--teal)"/></svg>
<section class="abs flavours"></section>
<h2 class="abs section-title serif" style="top:1520px;color:var(--white)">Our Flavours</h2>
<div class="flavour" style="left:120px"><div class="img" role="img" aria-label="Carrot cake cupcakes with cream cheese frosting"></div><h3>Carrot Cake</h3><p>Lorem ipsum dolor sit amet, consectetur adipiscing elit, sed do</p></div>
<div class="flavour" style="left:368px"><div class="img" role="img" aria-label="Chocolate frosted cupcake"></div><h3>Chocolate Cake</h3><p>Lorem ipsum dolor sit amet, consectetur adipiscing elit, sed do</p></div>
<div class="flavour" style="left:616px"><div class="img" role="img" aria-label="Vanilla cupcakes with chocolate sprinkles"></div><h3>Venila Cake</h3><p>Lorem ipsum dolor sit amet, consectetur adipiscing elit, sed do</p></div>
<div class="flavour" style="left:864px"><div class="img" role="img" aria-label="Cupcakes topped with nut crumble"></div><h3>creamy Cake</h3><p>Lorem ipsum dolor sit amet, consectetur adipiscing elit, sed do</p></div>
<div class="arrow light" style="left:39px;top:1726px">«</div>
<div class="arrow light" style="left:1120px;top:1726px">»</div>
<div class="btn dark" style="left:519px;top:2007px;width:162px;height:42px;background:var(--cocoa)">View More <span class="dot"></span></div>

<!-- testimonials -->
<h2 class="abs section-title serif" style="top:2190px">Customer Testimonials</h2>
<div class="tcard" style="left:-23px"></div>
<div class="avatar" role="img" aria-label="Customer photo" style="left:-67px;top:2335px"></div>
<div class="tname" style="left:79px;top:2332px">JHON SMITH</div>
<div class="stars" style="left:79px;top:2358px">★★★★★</div>
<div class="ttext" style="left:79px;top:2390px">Lorem ipsum dolor sit amet, consectetur adipiscing elit, sed do eiusmod tempor incididunt</div>

<div class="tcard" style="left:440px"></div>
<div class="avatar" role="img" aria-label="Customer photo" style="left:388px;top:2335px"></div>
<div class="tname" style="left:542px;top:2332px">JHON MATHEW</div>
<div class="stars" style="left:542px;top:2358px">★★★★★</div>
<div class="ttext" style="left:542px;top:2390px">Lorem ipsum dolor sit amet, consectetur adipiscing elit, sed do eiusmod tempor incididunt</div>

<div class="tcard" style="left:904px"></div>
<div class="avatar" role="img" aria-label="Customer photo" style="left:851px;top:2335px"></div>
<div class="tname" style="left:1005px;top:2332px">JHON SMITH</div>
<div class="stars" style="left:1005px;top:2358px">★★★★★</div>
<div class="ttext" style="left:1005px;top:2390px;width:240px">Lorem ipsum dolor sit amet, consectetur adipiscing elit, sed do eiusmod tempor incididunt</div>

<!-- occasion -->
<section class="abs occasion"></section>
<div class="ph" role="img" aria-label="Young athlete leaping while holding up a cupcake" style="left:900px;top:2580px;width:250px;height:486px;border-radius:120px 120px 60px 60px;background:radial-gradient(ellipse at 50% 40%,#b0252a 0%,#6e1a18 45%,rgba(42,12,5,0) 75%)"></div>
<h2 class="abs occ-title serif">Make Every Occasion Sweeter</h2>
<p class="abs occ-sub">Let us bring the sweetness to your special day with custom cupcake orders!</p>
<div class="btn" style="left:110px;top:2854px;width:271px;height:44px;background:var(--teal)">Request Custom Order <span class="dot"></span></div>
<svg class="abs" style="left:0;top:2960px" width="1200" height="60" viewBox="0 0 1200 60"><path d="M0 30 L30 14 L60 28 L95 10 L130 26 L160 12 L195 30 L230 16 L265 34 L300 14 L335 28 L370 10 L405 30 L440 16 L475 32 L510 12 L545 28 L580 14 L615 32 L650 16 L685 30 L720 10 L755 28 L790 14 L825 32 L860 16 L895 30 L930 12 L965 28 L1000 14 L1035 32 L1070 16 L1105 30 L1140 12 L1175 28 L1200 18 L1200 60 L0 60Z" fill="#fff"/></svg>

<!-- gallery -->
<h2 class="abs section-title serif" style="top:3118px">Our Gallery</h2>
<div class="gimg" role="img" aria-label="Chocolate frosted cupcakes on glass stands" style="left:120px;top:3178px;width:305px;height:326px;background:linear-gradient(160deg,#a0603e,#5a2a18)"></div>
<div class="gimg" role="img" aria-label="Ribbon cutting event with chamber ambassadors" style="left:445px;top:3212px;width:305px;height:328px;background:linear-gradient(180deg,#8c8a8a 0%,#6b5a5a 55%,#b8262a 100%)"></div>
<div class="gimg" role="img" aria-label="Flavoured milk bottles" style="left:771px;top:3212px;width:305px;height:328px;background:linear-gradient(180deg,#e9eef2 0%,#c8d6ea 50%,#d88aa8 100%)"></div>
<div class="gimg" role="img" aria-label="Team at a cupcake display table" style="left:120px;top:3522px;width:305px;height:356px;background:linear-gradient(180deg,#c9ccc6 0%,#5a5550 50%,#2c3c78 100%)"></div>
<div class="gimg" role="img" aria-label="Staff outside the cupcake shop storefront" style="left:445px;top:3552px;width:635px;height:326px;background:linear-gradient(90deg,#6f6f6f 0%,#a8a8a8 45%,#5c5c5c 100%)"></div>
<div class="arrow teal" style="left:39px;top:3626px">«</div>
<div class="arrow teal" style="left:1120px;top:3626px">»</div>

<!-- goodness + footer -->
<svg class="abs" style="left:0;top:4070px" width="1200" height="40" viewBox="0 0 1200 40"><path d="M0 22 L30 12 L60 26 L90 8 L130 24 L160 14 L200 30 L1000 30 L1040 12 L1075 26 L1110 8 L1140 24 L1170 10 L1200 20 L1200 40 L0 40Z" fill="#000"/></svg>
<section class="abs footer"></section>
<div class="abs goodness-box"></div>
<h2 class="abs good-title serif">Goodness On the Go</h2>
<p class="abs good-sub">Layered perfection in a jar—easy to carry, impossible to resist!</p>
<div class="btn dark" style="left:519px;top:4159px;width:162px;height:42px;background:var(--cocoa)">Shop Jars <span class="dot"></span></div>
<div class="ph" role="img" aria-label="Pink cupcake with sprinkles" style="left:66px;top:3979px;width:133px;height:151px;border-radius:60px 60px 24px 24px;background:linear-gradient(180deg,#fbe8e4 0%,#f4cfc8 50%,#e89cb3 100%)"></div>
<div class="ph" role="img" aria-label="Pink cupcake with sprinkles" style="left:978px;top:4068px;width:135px;height:150px;border-radius:60px 60px 24px 24px;background:linear-gradient(180deg,#fbe8e4 0%,#f4cfc8 50%,#e89cb3 100%)"></div>

<div class="abs f-brand">Marbrook<br>Cupcakes</div>
<nav class="fnav">
  <a style="left:307px">Home</a>
  <a style="left:376px">About Us</a>
  <a style="left:466px">Order Online</a>
  <a style="left:582px">Flavours</a>
  <a style="left:668px">Shop</a>
  <a style="left:732px">Get Offer</a>
  <a style="left:822px">Contact Us</a>
</nav>
<div class="social" style="left:985px"></div>
<div class="social" style="left:1019px"></div>
<div class="social" style="left:1053px"></div>
<div class="abs f-offer">Offer Notifications !<br>You Want To Get ? Just Subscribe</div>
<div class="abs f-email">Enter Email<span class="go">»</span></div>
<div class="abs f-rule"></div>
<div class="abs copy">Copyright@2025. All Rights Reserved</div>

</body>
</html>
```